Dental Practice Billboard Design

We are a newer dental practice in need of a simple but appealing billboard for our growing dental practice to attract new patients. The practice is owned by husband and wife dentists and is family friendly in a small town in Kentucky. We try to be very friendly and caring to our patients. Would prefer a blue background for the billboard and our tooth logo to be prominent. We are partial to the Patua One font used in the image below but please feel free to tweak it as you deem necessary. The shape of the uppercase D and lowercase g are why we like that font, so fonts with a similarly shaped “D” and “g” would work as well. Please include our phone number (555) 847-1390. Please see our website Harlowbrookdentistry.example for more info on the practice if needed. Thank you! Looking forward to seeing your creation.
Updates

The dimensions will be 12ft x 24ft (3.6576m x 7.3152m). Apologies for not including this in the original prompt. Thank you all for your submissions.

Industry/Entity Type

Dental

Font styles to use
Other font styles liked:
• Patua One

Colors
0054AA
0677BA
7BADD7
CADEEF
E8F1F8
0094D4
00A9DD
6FCCEA
C7EBF8
E9F6FB
00AB8E
00BBA5
67D7C9
C6EFE9
E9F9F6
59FF00
82FF00
B8FF75
E3FFCB
F4FFEA

Requirements
Must have
• Phone number, website, Logo, Practice name “Harlow Brook Dentistry”
Should not have
• A tagline or slogan

```html
<!DOCTYPE html>
<html lang="en">
<head>
<meta charset="UTF-8">
<title>Harlow Brook Dentistry — Billboard</title>
<link href="https://fonts.googleapis.com/css2?family=Patua+One&display=swap" rel="stylesheet">
<style>
  :root {
    --page-bg: #e9edf2;
    --board-bg: #ffffff;
    --brand-blue: #41609f;
    --navy: #1f4b8b;
    --green: #2ea546;
    --green-light: #6cba45;
    --photo-a: #d9d4cf;
    --photo-b: #f3f1ee;
    --white: #ffffff;
  }
  * { margin: 0; padding: 0; box-sizing: border-box; }
  html, body {
    width: 1200px;
    height: 900px;
    overflow: hidden;
    background: var(--page-bg);
    font-family: "Patua One", Georgia, serif;
  }
  .billboard {
    position: absolute;
    left: 20px;
    top: 160px;
    width: 1160px;
    height: 580px;
    background: var(--board-bg);
    overflow: hidden;
    box-shadow: 0 10px 30px rgba(0, 0, 0, 0.15);
  }
  .team-photo {
    position: absolute;
    left: 30px;
    top: 28px;
    width: 390px;
    height: 524px;
    border-radius: 120px 120px 160px 160px;
    background: linear-gradient(160deg, var(--photo-b) 0%, var(--photo-a) 100%);
    border-left: 26px solid var(--brand-blue);
    border-right: 26px solid var(--green);
  }
  .practice-name {
    position: absolute;
    left: 470px;
    top: 70px;
    display: flex;
    align-items: center;
    gap: 20px;
    color: var(--brand-blue);
    font-size: 54px;
    line-height: 1;
    white-space: nowrap;
  }
  .practice-name .mark-dot {
    width: 34px;
    height: 34px;
    border-radius: 50%;
    background: var(--brand-blue);
    flex: none;
  }
  .headline {
    position: absolute;
    left: 468px;
    top: 205px;
    font-size: 86px;
    line-height: 1;
    font-weight: 400;
    white-space: nowrap;
  }
  .headline .word-family { color: var(--navy); }
  .headline .word-dentistry { color: var(--green); }
  .call-band {
    position: absolute;
    left: 452px;
    top: 348px;
    right: 0;
    height: 106px;
    display: flex;
  }
  .call-band .call-label {
    width: 230px;
    flex: none;
    background: linear-gradient(90deg, var(--green) 0%, var(--green-light) 100%);
    border-radius: 53px 0 0 53px;
    color: var(--white);
    font-size: 54px;
    display: flex;
    align-items: center;
    justify-content: center;
    padding-right: 34px;
  }
  .call-band .phone {
    flex: 1;
    background: var(--navy);
    border-radius: 40px 0 0 40px;
    margin-left: -30px;
    color: var(--white);
    font-size: 72px;
    display: flex;
    align-items: center;
    padding-left: 40px;
    white-space: nowrap;
  }
  .website {
    position: absolute;
    left: 478px;
    top: 484px;
    display: flex;
    align-items: center;
    gap: 14px;
    color: var(--navy);
    font-size: 36px;
    white-space: nowrap;
  }
  .website svg { width: 32px; height: 32px; flex: none; }
</style>
</head>
<body>
  <main class="billboard">
    <div class="team-photo" role="img" aria-label="Photograph of the two dentists, a woman and a man in white coats, smiling"></div>

    <div class="practice-name">
      <span class="mark-dot"></span>
      <span class="name-text">Harlow Brook Dentistry</span>
    </div>

    <h1 class="headline">
      <span class="word-family">Family</span>
      <span class="word-dentistry">Dentistry</span>
    </h1>

    <div class="call-band">
      <div class="call-label">CALL</div>
      <div class="phone">(555) 847-1390</div>
    </div>

    <div class="website">
      <svg viewBox="0 0 24 24" aria-hidden="true">
        <path d="M3 3 L12 21 L14 14 L21 12 Z" fill="#1f4b8b"/>
        <path d="M13 13 L21 21" stroke="#1f4b8b" stroke-width="3" stroke-linecap="round"/>
      </svg>
      <span>www.harlowbrookdentistry.example</span>
    </div>
  </main>
</body>
</html>
```